Marvane Pour Over Coffee Filter Packaging Design

We are a brand new company starting to sell coffee related products. The coffee filter that we are about to sell will be copper color. We are working on the exact product picture, but a temporary one will be in uploaded files.We want the box to be simple, yet elegant and not too flashy. We prefer black, rose gold, white design, but are open to other designs. The uploaded files are just samples of what we like. "Marvane" means "owl" in French, we want an owl to be on the logo. Coffee related logo design is best, but we are open to other ideas. Size of this particular packaging is 14x14x12 cm

Target Market(s)

Online Retail

Industry/Entity Type

It Company

Logo Text

"Marvane Products" and "Marvane"

Other font styles liked:
• Your choice

Colors

Designer to choose colors to be used in the design.

Requirements
Must have
• Owl on the logo. Product description in a word file attached.
Nice to have
• Read product description

```html
<!DOCTYPE html>
<html lang="en">
<head>
<meta charset="utf-8">
<title>Marvane Pour Over Coffee Filter – Box Dieline</title>
<link href="https://fonts.googleapis.com/css2?family=Oswald:wght@300;500;600&family=Raleway:wght@300;700&family=Tinos:wght@400;700&family=Caveat:wght@500&display=swap" rel="stylesheet">
<style>
  :root{
    --stage:#a7a5a9;
    --paper:#f7f1e7;
    --paper-warm:#efe3cf;
    --brown:#7b4b34;
    --brown-dark:#4b3022;
    --rose:#e6a383;
    --ink:#3b2a22;
    --copper:#b7763d;
    --steel:#d9c9c4;
    --bean:#5a2e1c;
    --owl:#8a6238;
  }
  *{box-sizing:border-box;margin:0;padding:0}
  html,body{width:1200px;height:728px;overflow:hidden;background:var(--stage)}
  .dieline{
    position:absolute;left:20px;top:219px;width:1160px;height:290px;
    background:radial-gradient(ellipse at 35% 40%,var(--paper) 0%,var(--paper) 45%,var(--paper-warm) 100%);
    overflow:hidden;
  }
  .panel{position:absolute;top:0;height:290px}
  .half-left{left:0;width:585px}
  .half-right{left:585px;width:575px}

  .side-copy{position:absolute;left:30px;top:20px;width:178px;font-family:"Tinos",serif;color:var(--ink)}
  .side-copy h3{font-size:6.5px;font-weight:700;letter-spacing:.3px;margin-bottom:2px}
  .side-copy p{font-size:4.4px;line-height:1.35;margin-bottom:3px}
  .side-copy .tips{margin-top:6px}
  .thanks-art{float:right;width:34px;height:30px;margin:2px 0 2px 6px;border-radius:4px;background:var(--paper-warm)}
  .instructions{position:absolute;left:30px;top:196px;width:192px;border-left:1px solid var(--rose);padding-left:4px;font-family:"Oswald",sans-serif;color:var(--ink)}
  .instructions h3{font-size:5.5px;font-weight:600;margin-bottom:2px}
  .instructions li{font-size:4.1px;line-height:1.35;list-style:none;margin-bottom:2px;text-transform:uppercase;letter-spacing:.1px}

  .brand{position:absolute;display:flex;align-items:center;gap:5px;font-family:"Oswald",sans-serif;font-weight:600;color:var(--brown);line-height:1;white-space:nowrap}
  .brand .dot{border-radius:50%;background:var(--brown);flex:none}
  .brand-front{left:406px;top:40px;font-size:34px}
  .brand-front .dot{width:24px;height:24px}
  .brand-right{left:321px;top:26px;font-size:26px}
  .brand-right .dot{width:19px;height:19px}
  .brand-small{left:28px;top:236px;font-size:26px}
  .brand-small .dot{width:19px;height:19px}

  .product-name{position:absolute;text-align:right;font-family:"Raleway",sans-serif;color:var(--brown);border-right:2px solid var(--rose)}
  .product-name span{display:block;line-height:1.13}
  .product-name .light{font-weight:300}
  .product-name .bold{font-weight:700}
  .name-front{right:30px;top:122px;padding-right:7px;font-size:19px;letter-spacing:.6px}
  .name-right{right:17px;top:22px;padding-right:5px;font-size:14.5px;letter-spacing:.4px}

  .filter-photo{position:absolute;border-radius:6px 6px 40% 40%;background:radial-gradient(ellipse at 50% 18%,var(--copper) 0%,#d8a272 22%,var(--steel) 48%,#e9dcd6 70%,transparent 100%)}
  .photo-front{left:222px;top:135px;width:198px;height:158px}
  .photo-right{left:221px;top:137px;width:212px;height:156px}
  .beans{position:absolute;border-radius:40%;background:radial-gradient(ellipse,var(--bean) 0%,rgba(90,46,28,.55) 55%,transparent 75%)}
  .beans-front{left:390px;top:230px;width:120px;height:66px}
  .beans-right{left:393px;top:230px;width:112px;height:66px}

  .owl-art{position:absolute;left:3px;top:38px;width:130px;height:130px;border-radius:40% 40% 30% 30%;background:radial-gradient(circle at 50% 45%,var(--owl) 0%,#a7834f 50%,transparent 72%)}
  .bubble{position:absolute;left:128px;top:36px;width:142px;height:68px}
  .bubble-text{position:absolute;left:148px;top:45px;width:110px;font-family:"Caveat",cursive;font-size:11.5px;line-height:1.15;color:var(--ink)}

  .features{position:absolute;left:455px;top:140px;width:118px;list-style:none;font-family:"Oswald",sans-serif;font-weight:300;color:var(--ink)}
  .features li{display:flex;gap:4px;font-size:4.3px;line-height:1.35;margin-bottom:6px}
  .features svg{flex:none;width:8px;height:7px;margin-top:1px}
</style>
</head>
<body>
<main class="dieline">

  <section class="panel half-left">
    <div class="side-copy">
      <h3>HELLO THERE!</h3>
      <div class="thanks-art" role="img" aria-label="Hand lettered thank you note"></div>
      <p>Thank you for purchasing one of the Marvane Products! We hope you enjoy it! Here at Marvane, we like our coffee fresh and hot and so we strive to share our experience with you! We have put together a few tips on how to make your coffee experience the best, so check it out!</p>
      <p>Word of Wisdom from the Marvane Team: A good cup of coffee shared with a friend is like capturing happiness in a cup! Share the liquid gold (coffee that is) with others!</p>
      <h3 class="tips">TIPS AND TRICKS:</h3>
      <p>To make the best cup of coffee, make sure your grind is not too coarse and not too fine. It has to be just right! We generally recommend a medium-coarse grind to achieve the best results.</p>
      <p>The darker the roast of your coffee the more "spicy" and bittersweet it will taste. Light roasts retain more of the caffeine from the coffee bean. The optimum temperature for pour over coffee water is 195 to 205 degrees Fahrenheit. Bring your water to a boil and let it sit for about 30 seconds.</p>
      <p>Pre-infusion: this is a very important step when using a pour over coffee filter. Pour just enough water onto coffee to allow water to soak through the grounds. Give it a minute or so before brewing your coffee.</p>
      <p>We recommend keeping the spout of the kettle as close to the brew bed as possible, pouring over — not through — the coffee bed. After pre-infusion, pour softly in a circular pattern.</p>
    </div>

    <div class="instructions">
      <h3>INSTRUCTIONS</h3>
      <ol>
        <li>1. Place filter on your favorite mug and fill with a desired amount of coffee. We recommend 2-3 teaspoons per one cup of coffee.</li>
        <li>2. Pre-infuse your coffee by pouring just enough hot water to allow water to soak through the grounds. Wait for 30 seconds.</li>
        <li>3. Pour desired amount of water onto your pre-infused coffee in circular motion. Be careful not to pour too much water at once.</li>
        <li>4. It should take about three minutes for a 6 ounce cup of coffee to finish dripping.</li>
        <li>5. Sit back and enjoy your cup of coffee.</li>
      </ol>
    </div>

    <div class="filter-photo photo-front" role="img" aria-label="Photo of the copper and steel pour over coffee filter"></div>
    <div class="beans beans-front" role="img" aria-label="Roasted coffee beans"></div>

    <div class="brand brand-front"><span class="dot"></span><span>MARVANE</span></div>
    <h2 class="product-name name-front"><span class="light">POUR OVER</span><span class="bold">COFFEE</span><span class="bold">FILTER</span></h2>
  </section>

  <section class="panel half-right">
    <div class="owl-art" role="img" aria-label="Illustrated owl perched on a branch holding a coffee cup"></div>
    <svg class="bubble" viewBox="0 0 142 68" aria-hidden="true">
      <path d="M20 30 C20 10 50 3 80 3 C115 3 139 15 139 34 C139 55 112 65 80 65 C50 65 24 56 20 42 L4 46 L19 36 Z" fill="none" stroke="#8a6a58" stroke-width="0.8"/>
    </svg>
    <p class="bubble-text">Don't miss out.<br>Enjoy your Coffee<br>at its best</p>

    <div class="brand brand-small"><span class="dot"></span><span>MARVANE</span></div>

    <div class="filter-photo photo-right" role="img" aria-label="Photo of the copper and steel pour over coffee filter"></div>
    <div class="beans beans-right" role="img" aria-label="Roasted coffee beans"></div>

    <div class="brand brand-right"><span class="dot"></span><span>MARVANE</span></div>
    <h2 class="product-name name-right"><span class="light">POUR OVER</span><span class="bold">COFFEE</span><span class="bold">FILTER</span></h2>

    <ul class="features">
      <li><svg viewBox="0 0 8 7"><path d="M0 1h8M0 3.5h8M0 6h8" stroke="#3b2a22" stroke-width=".8"/></svg><span>The perfect alternative to disposable paper filters, which rob your coffee of essential oils and nutrients.</span></li>
      <li><svg viewBox="0 0 8 7"><rect x="1" y="1" width="5" height="5.5" fill="none" stroke="#3b2a22" stroke-width=".8"/></svg><span>Designed to fit on most cups, mugs, thermoses, small pots, and even carafes.</span></li>
      <li><svg viewBox="0 0 8 7"><path d="M0 6L7 1M4 1h3v3" fill="none" stroke="#3b2a22" stroke-width=".8"/></svg><span>Laser cut 18/10 stainless double filter ensures that no grounds end up in your cup.</span></li>
      <li><svg viewBox="0 0 8 7"><path d="M4 0.5C2 3 1.5 4 1.5 5a2.5 2 0 0 0 5 0C6.5 4 6 3 4 .5Z" fill="none" stroke="#3b2a22" stroke-width=".8"/></svg><span>Our pour over coffee filter does not absorb essential oils from coffee beans, allowing you to make a perfectly clear and flavorful coffee every single time.</span></li>
      <li><svg viewBox="0 0 8 7"><ellipse cx="4" cy="3.5" rx="3.5" ry="2" fill="none" stroke="#3b2a22" stroke-width=".8"/><circle cx="4" cy="3.5" r="1" fill="#3b2a22"/></svg><span>Reusable and easy to clean - simply rinse well with warm water or throw it into the dishwasher.</span></li>
    </ul>
  </section>

</main>
</body>
</html>
```